Business Card - Tidal Lanes

Need Business Card design for company named Tidal Lanes. Software development focused mainly on Brindle Orvix & Zelt Apps. I've attached our logo with both a black and white background. Please add trademark symbol to logo when using.

```html
<!DOCTYPE html>
<html lang="en">
<head>
<meta charset="utf-8">
<title>Tidal Lanes – Business Card</title>
<link rel="stylesheet" href="https://fonts.googleapis.com/css2?family=Montserrat:wght@400;600;700&display=swap">
<style>
  :root {
    --backdrop: #e9e6e1;
    --ink-black: #0b0b0b;
    --sun-yellow: #f7c21a;
    --deep-orange: #f49a2c;
    --accent-red: #d4202a;
    --name-orange: #f39a1e;
    --text-white: #ffffff;
    --text-dark: #3a2a10;
    --divider: #8a8a8a;
  }
  * { margin: 0; padding: 0; box-sizing: border-box; }
  html, body {
    width: 1200px; height: 720px; overflow: hidden;
    background: var(--backdrop);
    font-family: "Montserrat", sans-serif;
  }
  .canvas {
    position: relative; width: 1200px; height: 720px;
    display: flex; align-items: center; justify-content: center; gap: 40px;
  }
  .card {
    position: relative; width: 540px; height: 309px;
    overflow: hidden; border-radius: 3px;
    box-shadow: 0 6px 18px rgba(0,0,0,0.18);
  }
  .card-shape { position: absolute; inset: 0; width: 100%; height: 100%; }

  /* Front */
  .brand {
    position: absolute; left: 44px; top: 96px;
    display: flex; align-items: center; gap: 10px;
  }
  .brand-mark { width: 18px; height: 18px; background: var(--name-orange); }
  .brand-name {
    color: var(--text-white); font-weight: 700; font-size: 30px; letter-spacing: -0.5px;
  }
  .contact-divider {
    position: absolute; left: 284px; top: 58px; width: 1px; height: 78px;
    background: linear-gradient(to bottom, transparent, var(--divider), transparent);
  }
  .contact {
    position: absolute; left: 300px; top: 56px; color: var(--text-white);
  }
  .contact-name { color: var(--name-orange); font-weight: 700; font-size: 17px; line-height: 1.2; }
  .contact-title { font-size: 13px; line-height: 1.4; margin-bottom: 6px; }
  .contact-line { display: flex; align-items: center; gap: 8px; font-size: 13px; line-height: 1.65; }
  .contact-line svg { width: 11px; height: 13px; flex: none; }
  .address {
    position: absolute; left: 0; right: 0; bottom: 28px; text-align: center;
    color: var(--text-dark); font-size: 12px; font-weight: 600; letter-spacing: 0.4px;
    padding-left: 60px;
  }

  /* Back */
  .card-back { background: linear-gradient(120deg, var(--sun-yellow), var(--deep-orange)); }
  .back-name {
    position: absolute; inset: 0; display: flex; align-items: center; justify-content: center;
    color: var(--text-white); font-weight: 700; font-size: 48px; letter-spacing: -1px;
  }
</style>
</head>
<body>
<main class="canvas">
  <section class="card card-front">
    <svg class="card-shape" viewBox="0 0 540 309" preserveAspectRatio="none" aria-hidden="true">
      <defs>
        <linearGradient id="frontWarm" x1="0" y1="0" x2="1" y2="0">
          <stop offset="0" stop-color="#f6a32a"/>
          <stop offset="1" stop-color="#f8c51b"/>
        </linearGradient>
      </defs>
      <rect width="540" height="309" fill="var(--ink-black)"/>
      <path d="M0 244 C 170 290, 360 215, 540 112 L540 309 L0 309 Z" fill="var(--accent-red)"/>
      <path d="M0 252 C 170 298, 360 224, 540 124 L540 309 L0 309 Z" fill="url(#frontWarm)"/>
    </svg>

    <div class="brand">
      <span class="brand-mark"></span>
      <span class="brand-name">Tidal Lanes</span>
    </div>

    <div class="contact-divider"></div>
    <div class="contact">
      <p class="contact-name">Your Name</p>
      <p class="contact-title">Title</p>
      <p class="contact-line">
        <svg viewBox="0 0 11 13"><rect x="1.5" y="0.5" width="8" height="12" rx="1.5" fill="var(--sun-yellow)"/><rect x="3" y="2" width="5" height="7" fill="var(--ink-black)"/></svg>
        813-555-0142
      </p>
      <p class="contact-line">
        <svg viewBox="0 0 11 13"><path d="M2 3 Q1 3 1 5 Q2 9 6 11 Q8 12 8.5 10.5 L9.5 9 L7 7.5 L6 8.5 Q4 7.5 3.5 5.5 L4.5 4.5 L3 2 Z" fill="var(--sun-yellow)"/></svg>
        813-555-0187
      </p>
    </div>

    <p class="address">2440 Harbor Row, Bayfield, FL 33561</p>
  </section>

  <section class="card card-back">
    <p class="back-name">Tidal Lanes</p>
  </section>
</main>
</body>
</html>
```